Cobalt Ridge Electric Needs A Logo Design

We need a logo for my new company based out of Sacramento, Ca called Cobalt Ridge Electric. The name says it all, my electrical contracting business provides "Cobalt Ridge Professional Work" I'm open to any colors that pop and customers to say Wow. I would love to print my cards on metal.

Industry/Entity Type

Business

Contact Information for Business Card

The card needs to have as follows
Name of company: Cobalt Ridge Electric
My Name: Marco Delvane
Phone # 916-555-0173
CL# 2049381
Email: cobaltridgeelectric@mailnest.example
and a slogan that represent "COBALT RIDGE"

Requirements
Must have
• The card needs to have as follows
• Name of company: Cobalt Ridge Electric
• My Name : Marco Delvane
• Phone # 916-555-0173
• CL# 2049381
• Email: cobaltridgeelectric@mailnest.example
• and a slogan that represent "COBALT RIDGE"
Nice to have
• popping colors
• electrical Arcing

```html
<!DOCTYPE html>
<html lang="en">
<head>
<meta charset="UTF-8">
<title>Cobalt Ridge Electric — Business Card</title>
<link rel="stylesheet" href="https://fonts.googleapis.com/css2?family=Montserrat:wght@400;500;700&display=swap">
<style>
  :root {
    --backdrop: #e9e6e1;
    --card: #fbfbfa;
    --brand-blue: #0aa3dc;
    --brand-red: #e8473f;
    --card-shadow: rgba(0, 0, 0, 0.18);
  }
  html, body {
    margin: 0;
    padding: 0;
    width: 1200px;
    height: 1022px;
    overflow: hidden;
    background: var(--backdrop);
    font-family: "Montserrat", Arial, sans-serif;
  }
  .business-card {
    position: absolute;
    left: 100px;
    top: 225px;
    width: 1000px;
    height: 572px;
    background: var(--card);
    box-shadow: 0 10px 30px var(--card-shadow);
  }
  .brand {
    position: absolute;
    left: 70px;
    top: 120px;
    display: flex;
    align-items: flex-end;
    gap: 22px;
  }
  .brand-square {
    width: 120px;
    height: 120px;
    background: var(--brand-red);
  }
  .brand-name {
    color: var(--brand-blue);
    font-weight: 500;
    font-size: 30px;
    letter-spacing: 1px;
    line-height: 1;
    text-transform: uppercase;
    padding-bottom: 2px;
  }
  .divider {
    position: absolute;
    left: 0;
    right: 0;
    top: 300px;
    height: 3px;
    background: var(--brand-red);
  }
  .holder-name {
    position: absolute;
    right: 60px;
    top: 276px;
    padding: 0 18px;
    background: var(--card);
    color: var(--brand-blue);
    font-weight: 700;
    font-size: 44px;
    line-height: 50px;
    letter-spacing: 1px;
    text-transform: uppercase;
  }
  .contact-list {
    position: absolute;
    left: 70px;
    top: 340px;
    margin: 0;
    padding: 0;
    list-style: none;
  }
  .contact-item {
    display: flex;
    align-items: center;
    gap: 16px;
    color: var(--brand-blue);
    font-size: 28px;
    line-height: 46px;
  }
  .contact-icon {
    width: 22px;
    height: 22px;
    flex: none;
  }
</style>
</head>
<body>
  <main class="business-card">
    <div class="brand">
      <div class="brand-square"></div>
      <div class="brand-name">Cobalt Ridge Electric</div>
    </div>

    <div class="divider"></div>
    <div class="holder-name">Marco Delvane</div>

    <ul class="contact-list">
      <li class="contact-item">
        <svg class="contact-icon" viewBox="0 0 22 22" aria-hidden="true">
          <rect x="3" y="2" width="16" height="18" rx="2" fill="none" stroke="#e8473f" stroke-width="2"/>
          <line x1="7" y1="8" x2="15" y2="8" stroke="#e8473f" stroke-width="2"/>
        </svg>
        <span>2049381</span>
      </li>
      <li class="contact-item">
        <svg class="contact-icon" viewBox="0 0 22 22" aria-hidden="true">
          <path d="M6 3 L9 3 L10 7 L8 9 C9 12 11 14 13 15 L15 13 L19 14 L19 17 C19 18 18 19 17 19 C10 19 3 12 3 5 C3 4 4 3 6 3 Z" fill="none" stroke="#e8473f" stroke-width="2" stroke-linejoin="round"/>
        </svg>
        <span>916-555-0173</span>
      </li>
      <li class="contact-item">
        <svg class="contact-icon" viewBox="0 0 22 22" aria-hidden="true">
          <rect x="2" y="4" width="18" height="14" rx="1" fill="none" stroke="#e8473f" stroke-width="2"/>
          <polyline points="6,11 10,15 16,8" fill="none" stroke="#e8473f" stroke-width="2"/>
        </svg>
        <span>cobaltridgeelectric@mailnest.example</span>
      </li>
    </ul>
  </main>
</body>
</html>
```